New Business Card Design Project

We require a business card design for Vexalund, a newly established Indian company.
Our focus is on the development, manufacturing, and export of a diverse array of pharmaceutical products on a global scale. The card should convey a professional appearance, as our primary markets are in Africa, China, and Southeast Asian nations.
We envision a two-sided business card, with the reverse side dedicated to a logo set against a solid color or an elegantly designed pattern. The corners should be rounded. We would appreciate seeing both horizontal and vertical design options. We trust the designer to utilize their expertise in creating this design.

The content for the business card is included in the attached Word file.

Target Market(s)

Our primary markets are in Africa, China, and Southeast Asian, Latin America, Maldives, Sri Lanka

Industry/Entity Type

Pharmaceutical Manufacturing and Export

Contact Information for Business Card

Colors

Designer to choose colors to be used in the design.

Requirements
Must have
• The reverse side of the business card features solely the logo along with the tagline, "Remedies of Life."
Should not have
• The logo should not exceed two instances, encompassing both the front and back sides of the card.

```html
<!DOCTYPE html>
<html lang="en">
<head>
<meta charset="utf-8">
<title>Vexalund Business Card</title>
<link rel="stylesheet" href="https://fonts.googleapis.com/css2?family=Poppins:wght@400;600;700&display=swap">
<style>
  :root {
    --bg: #c9c9c9;
    --card-white: #ffffff;
    --brand-blue: #27a9e1;
    --brand-red: #f0604d;
    --tint-blue: rgba(39,169,225,0.13);
    --tint-red: rgba(240,96,77,0.12);
    --pattern-dark: rgba(10,110,170,0.22);
    --pattern-light: rgba(255,255,255,0.10);
    --ink: #3a3a3a;
    --rule: #5bbde6;
  }
  * { margin: 0; padding: 0; box-sizing: border-box; }
  html, body { width: 1200px; height: 802px; overflow: hidden; }
  body {
    background: var(--bg);
    font-family: "Poppins", sans-serif;
    display: flex;
    align-items: center;
    justify-content: center;
    gap: 50px;
  }
  .card {
    width: 530px;
    height: 303px;
    border-radius: 22px;
    position: relative;
    overflow: hidden;
    box-shadow: 0 8px 24px rgba(0,0,0,0.22);
  }
  .card-front { background: var(--card-white); }

  /* soft background tint areas on the front */
  .front-tint {
    position: absolute;
    inset: 0;
    background:
      radial-gradient(ellipse 150px 110px at 130px 230px, var(--tint-blue), transparent 75%),
      radial-gradient(ellipse 190px 90px at 300px 120px, var(--tint-red), transparent 75%);
  }

  .brand-name {
    position: absolute;
    left: 40px;
    top: 24px;
    font-weight: 700;
    font-size: 56px;
    line-height: 1;
    color: var(--brand-blue);
    letter-spacing: 0.5px;
  }
  .person {
    position: absolute;
    left: 120px;
    top: 94px;
    display: flex;
    align-items: flex-end;
    gap: 14px;
  }
  .person-name {
    font-weight: 700;
    font-size: 21px;
    color: var(--brand-blue);
    line-height: 1.2;
  }
  .person-name .surname { color: var(--brand-red); }
  .person-role {
    font-size: 13px;
    color: var(--ink);
    line-height: 1.3;
    padding-bottom: 2px;
  }
  .divider {
    position: absolute;
    left: 32px;
    right: 32px;
    top: 170px;
    height: 1px;
    background: var(--rule);
  }
  .contact-list {
    position: absolute;
    left: 36px;
    top: 192px;
    list-style: none;
    font-size: 13px;
    color: var(--ink);
    line-height: 1.8;
  }
  .contact-list li { display: flex; align-items: center; gap: 8px; }
  .contact-list svg { width: 11px; height: 11px; flex: none; }
  .address {
    position: absolute;
    right: 32px;
    top: 192px;
    font-style: normal;
    font-size: 13px;
    color: var(--ink);
    line-height: 1.8;
  }

  .card-back { background: var(--brand-blue); }
  .back-pattern {
    position: absolute;
    inset: 0;
    background: linear-gradient(135deg, var(--pattern-light) 0%, transparent 45%, var(--pattern-dark) 100%);
  }
  .back-lockup {
    position: relative;
    height: 100%;
    display: flex;
    flex-direction: column;
    align-items: center;
    justify-content: center;
    gap: 4px;
  }
  .back-brand { display: flex; align-items: center; gap: 14px; }
  .back-mark {
    width: 24px;
    height: 24px;
    border-radius: 50%;
    background: var(--card-white);
  }
  .back-name {
    font-weight: 700;
    font-size: 58px;
    line-height: 1.1;
    color: var(--card-white);
    letter-spacing: 0.5px;
  }
  .back-tagline {
    font-size: 15px;
    font-weight: 400;
    color: var(--card-white);
    letter-spacing: 3px;
    text-transform: uppercase;
    padding-left: 38px;
  }
</style>
</head>
<body>
  <section class="card card-front" aria-label="Card front">
    <div class="front-tint" role="img" aria-label="Soft blue and coral background decoration"></div>
    <div class="brand-name">Vexalund</div>
    <div class="person">
      <div class="person-name">Rohan K. <span class="surname">Sathe</span></div>
      <div class="person-role">CEO<br>Vexalund</div>
    </div>
    <div class="divider"></div>
    <ul class="contact-list">
      <li>
        <svg viewBox="0 0 12 12" aria-hidden="true"><path fill="#f0604d" d="M2.5 1h2l1 2.7-1.3.9a6.5 6.5 0 0 0 3.2 3.2l.9-1.3 2.7 1v2a1.5 1.5 0 0 1-1.6 1.5A9.5 9.5 0 0 1 1 2.6 1.5 1.5 0 0 1 2.5 1z"/></svg>
        +919876501234
      </li>
      <li>
        <svg viewBox="0 0 12 12" aria-hidden="true"><rect x="1" y="2.5" width="10" height="7" rx="1" fill="#f0604d"/><path d="M1.5 3l4.5 3.5L10.5 3" stroke="#fff" stroke-width="1" fill="none"/></svg>
        rsathe@vexalund.com
      </li>
      <li>
        <svg viewBox="0 0 12 12" aria-hidden="true"><circle cx="6" cy="6" r="5" fill="#f0604d"/><path d="M1 6h10M6 1c2 2.5 2 7.5 0 10M6 1c-2 2.5-2 7.5 0 10" stroke="#fff" stroke-width="0.8" fill="none"/></svg>
        www.vexalund.com
      </li>
    </ul>
    <address class="address">
      Plot No.14, Sunrise Colony<br>
      Kamal Road, Ravipur<br>
      Pin Code: 441100, Maharashtra, India
    </address>
  </section>

  <section class="card card-back" aria-label="Card back">
    <div class="back-pattern" role="img" aria-label="Subtle tone-on-tone background pattern"></div>
    <div class="back-lockup">
      <div class="back-brand">
        <span class="back-mark"></span>
        <span class="back-name">Vexalund</span>
      </div>
      <div class="back-tagline">Remedies of Life</div>
    </div>
  </section>
</body>
</html>
```